Mental Health care Company in Washington DC

We are a new mental health care services provider in Washington DC. Please look at these sites.
https://brightwaterfamilysupport.com
https://www.quietharborinc.com
https://willowgate-dc.org/
https://www.tidepathdc.com
https://www.thelanternofdc.com

```html
<!DOCTYPE html>
<html lang="en">
<head>
<meta charset="utf-8">
<title>Solace Health Services – Mental Health Care in Washington DC</title>
<link rel="stylesheet" href="https://fonts.googleapis.com/css2?family=Poppins:wght@400;500;600;700&display=swap">
<style>
:root{
  --navy:#0c2444;
  --orange:#f47e22;
  --peach:#f6a863;
  --teal:#3aa6b9;
  --soft:#eef1f7;
  --sky:#b8dde3;
  --text:#333c4a;
  --muted:#5b6270;
  --line:#e3e6ec;
}
*{margin:0;padding:0;box-sizing:border-box}
html,body{width:1200px;height:4556px;overflow:hidden}
body{position:relative;font-family:"Poppins",sans-serif;color:var(--text);background:#fff}
.abs{position:absolute}
/* top bar */
.topbar{left:0;top:0;width:1200px;height:35px;background:var(--peach);font-size:11px;font-weight:500;color:var(--navy)}
.topbar .follow{left:137px;top:10px}
.social-sq{width:33px;height:35px;top:0;display:flex;align-items:center;justify-content:center}
.social-sq span{width:11px;height:11px;background:var(--navy);border-radius:2px}
.social-sq.active{background:#fff}
.topbar .contact{top:10px;display:flex;align-items:center;gap:8px}
.ico-dot{width:12px;height:12px;border-radius:50%;background:var(--navy)}
/* header */
.header{left:0;top:35px;width:1200px;height:87px;background:#fff}
.brand{display:flex;align-items:center;gap:10px;font-weight:500;color:var(--navy);font-size:30px;letter-spacing:-.5px}
.brand i{width:12px;height:12px;border-radius:50%;background:var(--orange);display:block}
.nav{left:524px;top:34px;display:flex;gap:45px;font-size:13px;font-weight:500;color:var(--navy)}
.btn-outline{left:916px;top:22px;width:140px;height:42px;border-radius:21px;background:var(--peach);display:flex;align-items:center;padding-left:20px;font-size:13px;font-weight:500;color:var(--navy)}
.btn-outline .arrow,.btn .arrow{position:absolute;right:5px;top:5px;width:32px;height:32px;border:1.5px solid var(--navy);border-radius:50%;display:flex;align-items:center;justify-content:center}
/* hero */
.hero-bg{left:0;top:122px}
.hero-photo{left:532px;top:178px;width:460px;height:460px;border-radius:50%;background:radial-gradient(circle at 40% 30%,#f3e3c0,#d6b46e 45%,#8f9a3e 75%,#5d6e2a)}
.hero-copy{left:138px;top:240px;color:#fff;width:400px}
.hero-copy .k1{font-size:33px;font-weight:400;line-height:1.2}
.hero-copy .k2{font-size:37px;font-weight:700;line-height:1.25}
.hero-copy .k3{font-size:31px;font-weight:400;line-height:1.3}
.hero-copy p{font-size:15.5px;line-height:1.65;margin-top:22px;color:#e8edf4;width:345px}
.btn{position:absolute;height:40px;border-radius:20px;background:var(--orange);color:#fff;font-size:13px;font-weight:500;display:flex;align-items:center;padding-left:22px}
.hero-btn{left:137px;top:498px;width:219px;background:var(--peach);color:var(--navy)}
/* common headings */
.eyebrow{font-size:13px;font-weight:500;color:var(--teal);letter-spacing:.3px;text-transform:uppercase}
.h2{font-size:30px;font-weight:600;color:var(--navy);line-height:1.25}
.center{left:0;width:1200px;text-align:center}
.spark{display:inline-block;width:8px;height:8px;background:var(--orange);transform:rotate(45deg);margin:8px 0 0}
/* about */
.about-ring{left:122px;top:800px;width:440px;height:428px;border-radius:50%;border-left:6px solid var(--orange);border-top:3px solid var(--orange)}
.about-photo{left:132px;top:802px;width:430px;height:424px;border-radius:50%;background:linear-gradient(135deg,#e9eef3,#c4d2de 50%,#9fb3c6)}
.about-copy{left:626px;top:820px;width:440px}
.about-copy p{font-size:12.5px;line-height:22.6px;color:var(--muted);margin-top:22px}
/* services */
.services{left:0;top:1303px;width:1200px;height:573px;background:var(--soft)}
.card{position:absolute;top:1509px;width:295px;height:229px;background:#fff;border-radius:10px;overflow:hidden;box-shadow:0 4px 14px rgba(12,36,68,.08)}
.card .img{height:174px}
.card .label{height:55px;display:flex;align-items:center;justify-content:space-between;padding:0 26px;font-size:15px;font-weight:500;color:var(--navy)}
.card.active .label{background:var(--orange);color:#fff}
.dots{display:flex;gap:10px;justify-content:center}
.dots span{width:16px;height:4px;border-radius:2px;background:#c9ced8}
.dots span.on{background:var(--orange)}
/* testimonials */
.tcard{position:absolute;top:2080px;width:361px;height:257px;background:#fff;border-radius:6px;box-shadow:0 4px 16px rgba(12,36,68,.09);padding:12px}
.tcard .inner{border:1px solid var(--line);height:100%;padding:24px 24px;border-radius:4px}
.tname{font-size:15px;font-weight:500;color:var(--navy)}
.stars{color:var(--orange);font-size:14px;letter-spacing:2px;margin-top:2px}
.tcard .rev{border-top:1px solid var(--line);margin-top:16px;padding-top:18px;font-size:12.5px;line-height:24px;color:var(--muted)}
.badge{position:absolute;right:34px;top:38px;width:30px;height:30px;border-radius:50%;background:#e6e9ef}
.quote{position:absolute;right:20px;bottom:-14px;font-size:110px;line-height:.6;font-weight:700;color:var(--teal);font-family:Georgia,serif;height:50px}
.arrowbox{position:absolute;top:1990px;width:37px;height:37px;display:flex;align-items:center;justify-content:center}
/* team */
.team{left:0;top:2450px;width:1200px;height:765px;background:var(--soft)}
.tphoto{position:absolute;top:2660px;width:288px;height:340px;border-radius:8px;background:linear-gradient(180deg,#e4e6ea,#d1d5dc)}
.tinfo{position:absolute;top:2957px;width:231px;height:132px;background:#fff;border-radius:8px;text-align:center;padding-top:20px;box-shadow:0 4px 14px rgba(12,36,68,.08)}
.tinfo b{display:block;font-size:17px;font-weight:500;color:var(--navy)}
.tinfo small{display:block;font-size:11.5px;color:var(--muted);margin-top:2px}
.tinfo .soc{display:flex;gap:14px;justify-content:center;margin-top:14px}
.tinfo .soc span{width:10px;height:10px;border-radius:50%;background:var(--orange)}
/* faq */
.faq{left:138px;top:3420px;width:919px;background:#fff;border:1px solid var(--line);z-index:2}
.faq-item{border-bottom:1px solid var(--line);height:69px;display:flex;align-items:center;padding-left:52px;font-size:14.5px;font-weight:500;color:var(--navy);position:relative}
.faq-item:last-child{border-bottom:none}
.faq-item .tog{position:absolute;right:22px;top:21px;width:28px;height:28px;border-radius:50%;background:var(--navy);color:#fff;display:flex;align-items:center;justify-content:center;font-size:18px;line-height:1}
.faq-item.open{height:147px;display:block;padding-top:34px;background:#f6f7fa;border-left:3px solid var(--orange);padding-left:49px}
.faq-item.open .tog{background:var(--orange);top:26px}
.faq-item.open p{font-size:12.5px;font-weight:400;color:var(--muted);line-height:23px;margin-top:14px;padding-right:60px}
/* footer */
.footer-bg{left:0;top:3735px}
.footer{color:#fff}
.fcol{position:absolute;top:4204px}
.fcol h4{font-size:17px;font-weight:500;padding-bottom:8px;border-bottom:1px solid #fff;display:inline-block}
.fcol ul{list-style:none;margin-top:18px;font-size:12px;line-height:31px;color:#dfe5ee}
.fcontact{display:flex;gap:14px;align-items:flex-start;font-size:12px;line-height:22px;color:#dfe5ee;margin-bottom:16px}
.fcontact .ic{flex:none;width:34px;height:34px;border-radius:50%;background:#fff;display:flex;align-items:center;justify-content:center}
.email-in{width:198px;height:36px;border-radius:18px;background:#fff;color:#8c93a0;font-size:11px;display:flex;align-items:center;padding-left:22px;margin-top:18px}
.sub{width:198px;height:38px;border-radius:19px;background:var(--orange);color:#fff;font-size:12px;font-weight:600;display:flex;align-items:center;justify-content:center;margin-top:14px}
</style>
</head>
<body>

<!-- top bar -->
<div class="abs topbar">
  <div class="abs follow">Follow Us:</div>
  <div class="abs social-sq active" style="left:201px"><span></span></div>
  <div class="abs social-sq" style="left:236px"><span></span></div>
  <div class="abs social-sq" style="left:270px"><span></span></div>
  <div class="abs social-sq" style="left:304px"><span></span></div>
  <div class="abs contact" style="left:778px"><span class="ico-dot"></span>123 456 7890</div>
  <div class="abs contact" style="left:915px"><span class="ico-dot" style="border-radius:2px"></span>info@solacehealth.com</div>
</div>

<!-- header -->
<div class="abs header">
  <div class="abs brand" style="left:137px;top:24px"><i></i>Solace Health</div>
  <nav class="abs nav"><span>Home</span><span>About Us</span><span>Services</span><span>Our Team</span></nav>
  <div class="abs btn-outline">Contact Us<span class="arrow"><svg width="10" height="10" viewBox="0 0 10 10"><path d="M3 1l4 4-4 4" stroke="#0c2444" stroke-width="1.5" fill="none"/></svg></span></div>
</div>

<!-- hero -->
<svg class="abs hero-bg" width="1200" height="620" viewBox="0 0 1200 620">
  <path d="M0 0H1200V500C1040 590 860 640 690 613C500 560 300 500 0 512Z" fill="#0c2444"/>
  <path d="M735 0H1200V540C1100 575 880 612 690 613C630 470 610 210 735 0Z" fill="#b8dde3"/>
</svg>
<div class="abs hero-photo" role="img" aria-label="Photo of a woman breathing freely in a sunlit grass field"></div>
<div class="abs hero-copy">
  <div class="k1">Compassionate</div>
  <div class="k2">Mental Health Care</div>
  <div class="k3">in Washington DC</div>
  <p>Your journey to wellness begins with understanding. We’re here to guide you every step of the way.</p>
</div>
<div class="btn hero-btn">Schedule Consultation<span class="arrow"><svg width="10" height="10" viewBox="0 0 10 10"><path d="M3 1l4 4-4 4" stroke="#0c2444" stroke-width="1.5" fill="none"/></svg></span></div>

<!-- about -->
<div class="abs about-ring"></div>
<div class="abs about-photo" role="img" aria-label="Photo of a doctor shaking hands with a patient in a bright clinic"></div>
<div class="abs about-copy">
  <div class="eyebrow">Who We Are <span style="display:inline-block;width:60px;height:1px;background:#d8dce3;vertical-align:middle;margin-left:10px"></span></div>
  <div class="h2" style="margin-top:12px">A Trusted Mental Health<br>Partner In DC</div>
  <p>Lorem Ipsum is simply dummy text of the printing and typesetting industry. Lorem Ipsum has been the industry's standard dummy text ever since the 1500s, when an unknown printer took a galley of type and scrambled it to make a type specimen book. It has survived not only five centuries, but also the leap into electronic typesetting, remaining essentially unchanged. It was popularised in the 1960s with the release of Veltrane sheets containing Lorem Ipsum passages, and more recently with desktop publishing software like Corvel PageSetter including versions of Lorem Ipsum</p>
</div>
<div class="btn" style="left:626px;top:1172px;width:193px;padding-left:0;justify-content:center;height:38px">Learn More About Us</div>

<!-- services -->
<div class="abs services"></div>
<div class="abs center eyebrow" style="top:1390px">Our Core Services</div>
<div class="abs center" style="top:1407px"><span class="spark"></span></div>
<div class="abs center h2" style="top:1432px">Transformative Services For Real Results</div>
<div class="card" style="left:135px"><div class="img" role="img" aria-label="Photo of a therapist listening to a client on a sofa" style="background:linear-gradient(135deg,#efe6dc,#d9c4b0)"></div><div class="label">Individual Therapy<svg width="16" height="16" viewBox="0 0 16 16"><path d="M3 13L13 3M6 3h7v7" stroke="#0c2444" stroke-width="1.5" fill="none"/></svg></div></div>
<div class="card active" style="left:450px"><div class="img" role="img" aria-label="Photo of a smiling medical team standing together" style="background:linear-gradient(135deg,#e3e7ec,#aeb9c7)"></div><div class="label">Support Groups<svg width="22" height="16" viewBox="0 0 22 16"><path d="M1 8h19M13 1l7 7-7 7" stroke="#fff" stroke-width="1.5" fill="none"/></svg></div></div>
<div class="card" style="left:766px"><div class="img" role="img" aria-label="Photo of a nurse counselling an older patient" style="background:linear-gradient(135deg,#cfe0ee,#7aa2c4)"></div><div class="label">Counseling<svg width="16" height="16" viewBox="0 0 16 16"><path d="M3 13L13 3M6 3h7v7" stroke="#0c2444" stroke-width="1.5" fill="none"/></svg></div></div>
<div class="abs center dots" style="top:1787px;display:flex"><span class="on"></span><span></span><span></span><span></span></div>

<!-- testimonials -->
<div class="abs eyebrow" style="left:137px;top:1964px">Client Testimonials <span style="display:inline-block;width:60px;height:1px;background:#d8dce3;vertical-align:middle;margin-left:10px"></span></div>
<div class="abs h2" style="left:137px;top:1995px">A Trusted Mental Health Partner In DC</div>
<div class="arrowbox" style="left:968px;background:var(--orange)"><svg width="10" height="12" viewBox="0 0 10 12"><path d="M7 1L2 6l5 5" stroke="#fff" stroke-width="1.8" fill="none"/></svg></div>
<div class="arrowbox" style="left:1021px;background:var(--navy)"><svg width="10" height="12" viewBox="0 0 10 12"><path d="M3 1l5 5-5 5" stroke="#fff" stroke-width="1.8" fill="none"/></svg></div>
<div class="tcard" style="left:135px"><div class="inner"><div class="tname">Mira Tolland</div><div class="stars">★★★★★</div><div class="rev">Lorem Ipsum is simply dummy text of the printing and typesetting industry. Lorem Ipsum has been the industry's standard dummy text ever since the 1500s.</div></div><span class="badge"></span><span class="quote">”</span></div>
<div class="tcard" style="left:527px"><div class="inner"><div class="tname">Jonah Pellerin</div><div class="stars">★★★★★</div><div class="rev">Lorem Ipsum is simply dummy text of the printing and typesetting industry. Lorem Ipsum has been the industry's standard dummy text ever since the 1500s.</div></div><span class="badge"></span><span class="quote">”</span></div>
<div class="tcard" style="left:918px"><div class="inner"><div class="tname">R. Halvorsen</div><div class="stars">★★★★★</div><div class="rev">Lorem Ipsum is simply dummy text of the printing and typesetting industry. Lorem Ipsum has been the industry's standard dummy text ever since the 1500s.</div></div><span class="badge"></span><span class="quote">”</span></div>

<!-- team -->
<div class="abs team"></div>
<div class="abs center eyebrow" style="top:2539px">Meet Our Team</div>
<div class="abs center" style="top:2556px"><span class="spark"></span></div>
<div class="abs center h2" style="top:2581px">Meet The Minds Behind The Mission</div>
<div class="tphoto" style="left:138px" role="img" aria-label="Portrait of a male doctor in a white coat"></div>
<div class="tphoto" style="left:454px" role="img" aria-label="Portrait of a female doctor in a white coat"></div>
<div class="tphoto" style="left:771px" role="img" aria-label="Portrait of a female doctor in a white coat with stethoscope"></div>
<div class="tinfo" style="left:165px"><b>Theo Marchetti</b><small>Anxiety Specialist</small><div class="soc"><span></span><span></span><span></span><span></span></div></div>
<div class="tinfo" style="left:482px"><b>Ines Varga</b><small>Trauma Expert</small><div class="soc"><span></span><span></span><span></span><span></span></div></div>
<div class="tinfo" style="left:800px"><b>Clara Denholm</b><small>Group Therapy Lead</small><div class="soc"><span></span><span></span><span></span><span></span></div></div>
<div class="abs center dots" style="top:3124px;display:flex"><span class="on"></span><span></span><span></span><span></span></div>

<!-- faq -->
<div class="abs center eyebrow" style="top:3305px">FAQs</div>
<div class="abs center" style="top:3322px"><span class="spark"></span></div>
<div class="abs center h2" style="top:3347px">Frequently Asked Questions</div>

<svg class="abs footer-bg" width="1200" height="821" viewBox="0 0 1200 821">
  <path d="M0 5C200 130 420 190 640 200C900 212 1080 280 1200 400V821H0Z" fill="#0c2444"/>
</svg>

<div class="abs faq">
  <div class="faq-item">Who Is Your Primary Target Audience?<span class="tog">+</span></div>
  <div class="faq-item">What Are The Top 3 Actions You Want Visitors To Take On The Website?<span class="tog">+</span></div>
  <div class="faq-item open">Do You Have Existing Branding Elements To Incorporate, Or Should The Design Start Fresh?<span class="tog">–</span><p>Lorem Ipsum is simply dummy text of the printing and typesetting industry. Lorem Ipsum has been the industry's standard dummy text ever since the 1500s.</p></div>
  <div class="faq-item">Are There Any Specific Services Or Features That Must Be Highlighted Or Integrated?<span class="tog">+</span></div>
  <div class="faq-item">What Is Your Preferred Timeline And Budget For Launching The Website?<span class="tog">+</span></div>
</div>

<!-- footer -->
<div class="footer">
  <div class="abs center" style="top:4106px;display:flex;justify-content:center"><div class="brand" style="color:#fff"><i></i>Solace Health</div></div>
  <div class="fcol" style="left:137px"><h4>Quick Links</h4><ul><li>Home</li><li>About Us</li><li>Services</li><li>Blog</li><li>FAQs</li></ul></div>
  <div class="fcol" style="left:334px"><h4>Useful Links</h4><ul><li>Contact Us</li><li>Privacy Policy</li><li>Terms &amp; Conditions</li></ul></div>
  <div class="fcol" style="left:540px;width:270px"><h4>Contact Us</h4>
    <div style="margin-top:18px">
      <div class="fcontact"><span class="ic"><svg width="12" height="16" viewBox="0 0 12 16"><path d="M6 15S1 9 1 6a5 5 0 0110 0c0 3-5 9-5 9z" fill="#f47e22"/><circle cx="6" cy="6" r="2" fill="#fff"/></svg></span><span>123, Lorem Ipsum is simply<br>dummy text of the printing</span></div>
      <div class="fcontact" style="align-items:center"><span class="ic"><svg width="14" height="14" viewBox="0 0 14 14"><path d="M3 1l2 3-1.5 1.5a8 8 0 005 5L10 9l3 2-1.5 2.5C6 13 1 8 .5 2.5z" fill="#f47e22"/></svg></span><span>Phone: (123)-456-7890</span></div>
      <div class="fcontact" style="align-items:center"><span class="ic"><svg width="16" height="12" viewBox="0 0 16 12"><rect width="16" height="12" rx="2" fill="#f47e22"/><path d="M1 1l7 5 7-5" stroke="#fff" fill="none"/></svg></span><span>info@solacementalhealth.com</span></div>
    </div>
  </div>
  <div class="fcol" style="left:852px"><h4>Newsletter</h4>
    <div style="font-size:12px;line-height:18px;color:#dfe5ee;margin-top:18px;width:210px">Join our subscribers list to get the latest news &amp; special offers.</div>
    <div class="email-in">Enter your email</div>
    <div class="sub">SUBSCRIBE NOW</div>
  </div>
  <div class="abs" style="left:66px;top:4480px;width:1060px;height:1px;background:#3a5070"></div>
  <div class="abs center" style="top:4500px;font-size:11px;color:#dfe5ee">Copyright © 2025 Solace Mental Health | All Rights Reserved.</div>
</div>

</body>
</html>
```